RWT Fittings Ltd Business Cards

We need a business card with our business logo. We provide window and door installations on high-rises in west coast British Colombia, Canada.

I would like my business information and details on one side of the card, and the other side the company name with logo

Target Market(s)

General Contractors

Industry/Entity Type

Construction

Contact Information for Business Card

one side i want my company name and logo in the dark theme logo that i provided

Requirements
Must have
• Marco Peltieri, 16045518293, RWTFittings@mailbox-demo.com, 1407-5194 Linden Row Burnaby BC, V5H 2K9, Owner & Manager

```html
<!DOCTYPE html>
<html lang="en">
<head>
<meta charset="utf-8">
<title>RWT Fittings Ltd – Business Cards</title>
<link rel="stylesheet" href="https://fonts.googleapis.com/css2?family=Roboto:wght@400;500;700;900&display=swap">
<style>
  :root {
    --stage: #252526;
    --card: #1e1f24;
    --card-edge: #29a9e1;
    --accent: #29a9e1;
    --ink-light: #f2f2f2;
    --ink-grey: #a9abae;
    --ink-faint: #2c2e34;
    --brand-grey: #9c9ea2;
  }
  * { box-sizing: border-box; margin: 0; padding: 0; }
  html, body {
    width: 1200px; height: 780px; overflow: hidden;
    background: var(--stage);
    font-family: "Roboto", Arial, sans-serif;
  }
  .sheet {
    position: relative; width: 1200px; height: 780px;
  }
  .card {
    position: absolute;
    width: 560px; height: 320px;
    background: var(--card);
    border-radius: 22px;
    border-bottom: 5px solid var(--card-edge);
    border-left: 3px solid var(--card-edge);
    overflow: hidden;
  }
  .card--front { left: 120px; top: 60px; }
  .card--back  { left: 520px; top: 400px; }

  /* Front: brand name */
  .brand {
    position: absolute; left: 0; right: 0; top: 50%;
    transform: translateY(-50%);
    display: flex; align-items: center; justify-content: center; gap: 16px;
  }
  .brand__mark {
    width: 34px; height: 34px; background: var(--accent);
  }
  .brand__name {
    font-weight: 700; font-size: 38px; letter-spacing: 1px;
    color: var(--brand-grey);
  }

  /* Back: faint brand name on the left */
  .brand-side {
    position: absolute; left: 26px; top: 50%;
    transform: translateY(-50%) rotate(-90deg);
    transform-origin: center;
    font-weight: 700; font-size: 30px; letter-spacing: 1px;
    color: var(--ink-faint);
    width: 0; white-space: nowrap;
    display: flex; justify-content: center;
  }

  /* Back: contact block */
  .contact {
    position: absolute; right: 34px; top: 34px;
    text-align: right;
  }
  .contact__tab {
    position: absolute; right: -34px; top: 8px;
    width: 30px; height: 40px; background: var(--accent);
  }
  .person__name {
    font-weight: 700; font-size: 30px; line-height: 1.1;
    padding-right: 6px;
  }
  .person__first { color: var(--accent); }
  .person__last  { color: var(--ink-grey); }
  .person__role {
    font-weight: 500; font-size: 14px; color: var(--ink-light);
    padding-right: 6px; margin-top: 2px;
  }
  .address {
    margin-top: 26px; font-size: 14px; line-height: 1.35;
    color: var(--ink-light); font-style: normal;
    padding-right: 26px;
  }
  .lines { margin-top: 18px; list-style: none; }
  .lines li {
    display: flex; align-items: center; justify-content: flex-end; gap: 8px;
    font-size: 14px; line-height: 1.6; color: var(--ink-light);
  }
  .lines svg { width: 18px; height: 18px; flex: none; }
</style>
</head>
<body>
<main class="sheet">

  <section class="card card--front" aria-label="Card front">
    <div class="brand">
      <span class="brand__mark"></span>
      <span class="brand__name">RWT Fittings Ltd</span>
    </div>
  </section>

  <section class="card card--back" aria-label="Card back">
    <div class="brand-side">RWT Fittings Ltd</div>

    <div class="contact">
      <span class="contact__tab"></span>
      <h1 class="person__name"><span class="person__first">Marco</span> <span class="person__last">Peltieri</span></h1>
      <p class="person__role">Owner &amp; Manager</p>

      <address class="address">
        1407-5194 Linden Row<br>
        Burnaby BC, V5H 2K9
      </address>

      <ul class="lines">
        <li>1 604 551 8293
          <svg viewBox="0 0 24 24" aria-hidden="true"><path fill="var(--accent)" d="M6.6 10.8a15.1 15.1 0 0 0 6.6 6.6l2.2-2.2c.3-.3.7-.4 1-.2 1.1.4 2.3.6 3.6.6.6 0 1 .4 1 1V20c0 .6-.4 1-1 1A17 17 0 0 1 3 4c0-.6.4-1 1-1h3.5c.6 0 1 .4 1 1 0 1.3.2 2.5.6 3.6.1.3 0 .7-.2 1z"/></svg>
        </li>
        <li>RWTFittings@mailbox-demo.com
          <svg viewBox="0 0 24 24" aria-hidden="true"><rect x="2" y="5" width="20" height="14" rx="2" fill="var(--accent)"/><path d="M3 6.5l9 6.5 9-6.5" fill="none" stroke="var(--card)" stroke-width="1.6"/></svg>
        </li>
      </ul>
    </div>
  </section>

</main>
</body>
</html>
```